Card design for orthopaedic surgeons working as The Brightwater Joint Centre

Business cards, letterhead

Colors

Designer to choose colors to be used in the design.

Requirements
Must have
• Late addition.
• Cards letterhead must have logos of
• Crestmoor Lindell College of Surgeons
• Varenwood Bone Health Association
Nice to have
• Back of card to have space for appointment time to be added by hand and some blank space for writing incidental other notes.

```html
<!DOCTYPE html>
<html lang="en">
<head>
<meta charset="utf-8">
<title>The Brightwater Joint Centre – Business Cards</title>
<link rel="stylesheet" href="https://fonts.googleapis.com/css2?family=Montserrat:wght@400&family=Open+Sans:wght@400&family=Arimo:wght@700&display=swap">
<style>
  :root {
    --navy: #0a3550;
    --sky: #2ea6ea;
    --ink: #1d1d1f;
    --paper: #ffffff;
    --backdrop: #e9ebee;
  }
  html, body {
    margin: 0;
    padding: 0;
    width: 1200px;
    height: 960px;
    overflow: hidden;
    background: var(--backdrop);
  }
  .sheet {
    position: relative;
    width: 1200px;
    height: 960px;
  }
  .card {
    position: absolute;
    left: 250px;
    width: 700px;
    height: 400px;
    background: var(--paper);
    box-shadow: 0 6px 22px rgba(0, 0, 0, 0.12);
    overflow: hidden;
  }
  .card--back { top: 50px; }
  .card--front { top: 500px; }

  .wordmark {
    font-family: "Montserrat", sans-serif;
    font-weight: 400;
    color: var(--navy);
    letter-spacing: -0.5px;
    white-space: nowrap;
  }
  .card--back .wordmark {
    position: absolute;
    top: 150px;
    left: 0;
    width: 100%;
    text-align: center;
    font-size: 38px;
  }
  .site-line {
    position: absolute;
    top: 252px;
    left: 0;
    width: 100%;
    text-align: center;
    font-family: "Open Sans", sans-serif;
    font-size: 17px;
    letter-spacing: 5px;
    color: var(--ink);
  }
  .site-line .site-name { color: var(--sky); }

  .card--front .wordmark {
    position: absolute;
    top: 34px;
    left: 40px;
    font-size: 28px;
  }
  .waves {
    position: absolute;
    inset: 0;
  }
  .person {
    position: absolute;
    top: 96px;
    left: 58px;
  }
  .person-name {
    margin: 0;
    font-family: "Arimo", sans-serif;
    font-weight: 700;
    font-size: 22px;
    color: var(--navy);
  }
  .person-title {
    margin: 2px 0 0;
    font-family: "Arimo", sans-serif;
    font-weight: 700;
    font-size: 15px;
    color: var(--sky);
  }
  .address {
    position: absolute;
    top: 168px;
    left: 40px;
    margin: 0;
    font-family: "Open Sans", sans-serif;
    font-style: normal;
    font-size: 14px;
    line-height: 21px;
    color: var(--ink);
  }
  .contact {
    position: absolute;
    right: 22px;
    top: 304px;
    margin: 0;
    padding: 0;
    list-style: none;
    font-family: "Open Sans", sans-serif;
    font-size: 16px;
    color: var(--paper);
  }
  .contact li {
    display: flex;
    justify-content: flex-end;
    align-items: center;
    gap: 12px;
    height: 27px;
  }
  .contact svg { width: 16px; height: 16px; flex: none; }
</style>
</head>
<body>
<main class="sheet">

  <section class="card card--back" aria-label="Business card back">
    <div class="wordmark">The Brightwater Joint Centre</div>
    <div class="site-line">www.<span class="site-name">brightwaterjoint</span>.com</div>
  </section>

  <section class="card card--front" aria-label="Business card front">
    <svg class="waves" viewBox="0 0 700 400" width="700" height="400" aria-hidden="true">
      <path d="M0,190 C190,262 430,282 700,262 L700,400 L0,400 Z" fill="var(--sky)"/>
      <path d="M0,208 C200,272 440,292 700,280" fill="none" stroke="var(--paper)" stroke-width="3"/>
      <path d="M0,238 C210,296 440,306 700,292" fill="none" stroke="var(--paper)" stroke-width="7"/>
      <path d="M0,244 C210,300 440,310 700,296 L700,400 L0,400 Z" fill="var(--navy)"/>
    </svg>

    <div class="wordmark">The Brightwater Joint Centre</div>

    <div class="person">
      <p class="person-name">Mara Ellison</p>
      <p class="person-title">Title</p>
    </div>

    <address class="address">Street Name, City Name<br>Zipcode - 012345</address>

    <ul class="contact">
      <li>012-345-6789
        <svg viewBox="0 0 16 16" aria-hidden="true"><circle cx="8" cy="8" r="7.5" fill="var(--paper)"/><path d="M5.2,4.2 L6.6,4 L7.3,6 L6.4,6.8 C6.9,7.9 7.8,8.9 9,9.5 L9.8,8.6 L11.8,9.3 L11.6,10.8 C8,11 5,8 5.2,4.2 Z" fill="var(--navy)"/></svg>
      </li>
      <li>info@brightwaterjoint.com
        <svg viewBox="0 0 16 16" aria-hidden="true"><circle cx="8" cy="8" r="7.5" fill="var(--paper)"/><rect x="3.8" y="5.2" width="8.4" height="5.8" fill="none" stroke="var(--navy)" stroke-width="1.1"/><path d="M3.8,5.2 L8,8.5 L12.2,5.2" fill="none" stroke="var(--navy)" stroke-width="1.1"/></svg>
      </li>
      <li>www.brightwaterjoint.com
        <svg viewBox="0 0 16 16" aria-hidden="true"><circle cx="8" cy="8" r="7.5" fill="var(--paper)"/><circle cx="8" cy="8" r="4.6" fill="none" stroke="var(--navy)" stroke-width="1"/><ellipse cx="8" cy="8" rx="2" ry="4.6" fill="none" stroke="var(--navy)" stroke-width="1"/><path d="M3.4,8 H12.6" stroke="var(--navy)" stroke-width="1"/></svg>
      </li>
    </ul>
  </section>

</main>
</body>
</html>
```